I need a SEO-friendly Wordpress website (making sure to style H1, H2, H3, etc correctly) for a Hawaii-based law firm called Meridian Crest Legal Group. Comparable websites include https://brvlaw.example/ and https://www.lomrit.example/ for design reference. The current copy on the TarnAdvocate.example website can be used.

```html
<!DOCTYPE html>
<html lang="en">
<head>
<meta charset="utf-8">
<title>Meridian Crest Legal Group — Kona Lawyers</title>
<link href="https://fonts.googleapis.com/css2?family=Lora:wght@400;700&family=Montserrat:wght@400;500;600&display=swap" rel="stylesheet">
<style>
:root{
  --maroon:#6b1d0a;
  --rust:#a84f14;
  --deep:#6e1f0b;
  --accent:#7a2a10;
  --ink:#222;
  --body:#444;
  --light:#eeeeee;
  --white:#fff;
  --serif:'Lora', Georgia, serif;
  --sans:'Montserrat', Arial, sans-serif;
}
*{box-sizing:border-box;margin:0;padding:0}
html,body{width:1200px;height:3875px;overflow:hidden}
body{position:relative;font-family:var(--sans);color:var(--body);background:var(--white)}
a{color:inherit;text-decoration:none}
.abs{position:absolute}

/* top bar */
.topbar{top:0;left:0;width:1200px;height:41px;background:var(--maroon);color:#f3e3da;font-family:var(--serif);font-size:15px}
.topbar .contact{left:90px;top:10px;display:flex;gap:18px;align-items:center}
.topbar svg{vertical-align:-2px;margin-right:8px}
.social{display:flex;gap:6px}
.social span{width:30px;height:30px;display:flex;align-items:center;justify-content:center}
.topbar .social{right:90px;top:5px}
.s-blue1{background:#3b5998}.s-blue2{background:#1da1f2}.s-gray{background:#6d7680}.s-gray2{background:#7c8289}.s-red{background:#e8483a}

/* header */
.header{top:41px;left:0;width:1200px;height:69px;background:var(--white);box-shadow:0 1px 4px rgba(0,0,0,.08);z-index:3}
.brand{left:90px;top:12px}
.brand-name{font-family:var(--serif);font-weight:700;font-size:20px;color:#111}
.brand-tag{font-size:11px;color:#222;margin-left:18px;margin-top:1px}
.nav{right:90px;top:26px;display:flex;gap:48px;font-family:var(--serif);font-size:14px;color:#222;text-transform:uppercase}

/* hero */
.hero{top:110px;left:0;width:1200px;height:511px;background:linear-gradient(90deg,#e9e2dc 0%,#d9cfc6 40%,#c9bfb5 60%,#a9b5c8 80%,#cfc6bd 100%)}
.hero .kicker{left:105px;top:48px;font-family:var(--serif);font-weight:700;font-size:22px;color:#1a1a1a}
.hero .sub{left:105px;top:83px;font-size:20px;color:#222}
.hero h1{left:106px;top:120px;width:560px;font-family:var(--serif);font-weight:700;font-size:38px;line-height:43px;color:var(--accent)}
.btn{left:107px;top:286px;width:183px;height:52px;border:2px solid var(--accent);border-radius:26px;color:var(--accent);font-weight:600;font-size:16px;display:flex;align-items:center;justify-content:center;gap:10px}

/* feature boxes */
.box{top:498px;height:275px;color:#f7e9df;padding:16px 14px;font-family:var(--serif);font-size:13px;line-height:26px;z-index:2}
.box h3{font-size:17px;font-weight:700;color:#fff;margin-bottom:8px;line-height:26px}
.box ul{list-style:none}
.box li{padding-left:16px;position:relative}
.box li:before{content:"";position:absolute;left:2px;top:10px;border-left:5px solid #f7e9df;border-top:3px solid transparent;border-bottom:3px solid transparent}
.box p{text-align:justify}
.b1{left:277px;width:269px;background:var(--rust)}
.b2{left:558px;width:271px;background:var(--deep)}
.b3{left:839px;width:271px;background:var(--rust)}

/* section labels */
.label{font-family:var(--serif);font-size:20px;color:var(--accent);display:flex;align-items:center;gap:14px}
.label:after{content:"";width:160px;height:1px;background:var(--accent)}
h2{font-family:var(--serif);font-weight:700;color:#111}

/* about */
.about-label{left:90px;top:878px}
.about h2{left:90px;top:915px;width:480px;font-size:36px;line-height:42px}
.about .lead{left:90px;top:1010px;width:420px;font-size:20px;line-height:30px;color:#444}
.about .copy{left:601px;top:880px;width:530px;font-size:14.5px;line-height:30.5px;color:#333}
.about .copy p{margin-bottom:10px}
.learn{left:601px;top:1212px;font-size:14px;color:#333}
.learn u{color:var(--accent)}
.dots{left:567px;top:1279px;display:flex;gap:14px}
.dots i{width:26px;height:3px;background:#c8c8c8;display:block}
.dots i:first-child{background:var(--rust)}

/* practice */
.prac-label{left:468px;top:1396px}
.prac-title{left:0;width:1200px;top:1428px;text-align:center;font-size:38px}
.tile{width:600px;height:334px;color:#fff}
.tile h3{position:absolute;font-family:var(--serif);font-weight:400;font-size:23px}
.tile p{position:absolute;font-size:14.5px;line-height:27px;width:410px}
.tile .more{position:absolute;font-size:14.5px}
.t1{left:0;top:1498px;background:linear-gradient(135deg,#8c3a24,#a85a3a 60%,#b9764e)}
.t2{left:600px;top:1498px;background:linear-gradient(135deg,#6f7fa6,#3b4c7e 45%,#6d6f76 80%,#b8b8b8)}
.t3{left:0;top:1832px;background:linear-gradient(180deg,#3c2414,#6b3c1e 50%,#8a4e24)}
.t4{left:600px;top:1832px;background:linear-gradient(180deg,#8a6a4a,#a7804e 50%,#7a5a38)}
.t1 h3,.t3 h3{left:90px}.t1 p,.t3 p,.t1 .more,.t3 .more{left:91px}
.t2 h3,.t4 h3{right:92px}.t2 p,.t4 p{right:92px;text-align:right}.t2 .more,.t4 .more{right:92px}

/* team */
.team-label{left:190px;top:2275px}
.team-title{left:190px;top:2305px;font-size:38px}
.card{top:2391px;width:385px;height:196px;background:#fff;box-shadow:0 2px 12px rgba(0,0,0,.14);padding:32px 30px 0 84px;font-size:14.5px;line-height:27px;color:#333}
.card h3{font-family:var(--serif);font-weight:400;font-size:19px;color:#222;margin-bottom:10px}
.card .more{color:#1f3a8a;font-size:14.5px;display:block;margin-top:8px}
.c1{left:187px}
.c2{left:629px;padding:32px 84px 0 12px;text-align:right}
.avatar{width:128px;height:128px;border-radius:50%;border:2px solid var(--rust);top:2425px;background:linear-gradient(135deg,#d8d3ce,#6b6560)}
.a1{left:123px}.a2{left:950px}

/* blog */
.blog{top:2700px;left:0;width:1200px;height:699px;background:linear-gradient(135deg,#a4541c,#8e4416 45%,#b8692e)}
.blog-label{left:468px;top:2805px}
.blog-label.label{color:#fbe3d3}.blog-label.label:after{background:#fbe3d3}
.blog-title{left:0;width:1200px;top:2836px;text-align:center;font-size:38px;color:#fff}
.post{top:2906px;width:328px;height:383px;background:#fff;border:4px solid #fff}
.post .img{height:176px}
.post .date{position:absolute;left:12px;top:12px;width:62px;height:62px;background:var(--maroon);color:#fff;font-weight:600;font-size:16px;line-height:20px;text-align:center;padding-top:11px}
.post h3{font-family:var(--sans);font-weight:500;font-size:16.5px;line-height:26px;color:#111;margin:18px 8px 12px}
.post p{font-size:14.5px;line-height:26px;color:#555;margin:0 8px}
.post .more{display:block;margin:12px 8px;color:var(--accent);font-weight:600;font-size:14.5px}
.p1{left:90px}.p2{left:436px}.p3{left:782px}
.p1 .img{background:linear-gradient(135deg,#b9a89c,#e9e4e0)}
.p2 .img{background:linear-gradient(135deg,#6c7f96,#d2d7dd)}
.p3 .img{background:linear-gradient(135deg,#d9cbb9,#9e7d5a)}

/* contact strip */
.strip{top:3399px;left:0;width:1200px;height:98px;background:var(--light)}
.strip .social{left:90px;top:35px}
.strip .social span{width:37px;height:34px}
.strip .item{top:33px;display:flex;align-items:center;gap:18px;font-family:var(--serif);font-size:16px;color:var(--accent)}
.ico{width:38px;height:36px;border:1px solid var(--accent);display:flex;align-items:center;justify-content:center;background:#fff}
.i1{left:627px}.i2{left:870px}

/* footer */
.f-brand{left:90px;top:3572px}
.f-text{left:90px;top:3637px;width:300px;font-size:13.5px;line-height:27px;color:#333}
.f-col{top:3587px}
.f-col h4{font-family:var(--serif);font-weight:700;font-size:19px;color:var(--accent);margin-bottom:14px}
.f-col a{display:block;text-decoration:underline;font-size:13.5px;line-height:27px;color:#333}
.fc1{left:429px}.fc2{left:617px}.fc3{left:864px}
.f-input{width:248px;height:44px;border:1px solid #ccc;font-size:13px;color:#777;padding:13px 12px;margin-bottom:10px}
.f-btn{width:248px;height:44px;background:var(--rust);color:#fff;font-weight:500;font-size:15px;display:flex;align-items:center;justify-content:center}
.copy-line{left:0;width:1200px;top:3843px;text-align:center;font-size:13px;color:#333}
</style>
</head>
<body>

<div class="abs topbar">
  <div class="abs contact">
    <span><svg width="14" height="14" viewBox="0 0 24 24" fill="#f3e3da"><path d="M6.6 10.8a15 15 0 006.6 6.6l2.2-2.2c.3-.3.7-.4 1-.2 1.1.4 2.3.6 3.6.6.6 0 1 .4 1 1V20c0 .6-.4 1-1 1A17 17 0 013 4c0-.6.4-1 1-1h3.5c.6 0 1 .4 1 1 0 1.3.2 2.5.6 3.6.1.3 0 .7-.2 1z"/></svg>+1.808.555.0142</span>
    <span>|</span>
    <span><svg width="16" height="16" viewBox="0 0 24 24" fill="none" stroke="#f3e3da" stroke-width="2"><path d="M22 2L11 13M22 2l-7 20-4-9-9-4z"/></svg>clients@tarnadvocate.example</span>
  </div>
  <div class="abs social">
    <span class="s-blue1"></span><span class="s-blue2"></span>
    <span class="s-gray"><svg width="14" height="14" viewBox="0 0 24 24" fill="#fff"><path d="M6 2h12v6H6zM3 9h18v8h-3v5H6v-5H3zm5 7v4h8v-4z"/></svg></span>
    <span class="s-gray2"><svg width="14" height="12" viewBox="0 0 24 20" fill="#fff"><path d="M0 0h24v3L12 10 0 3zm0 6l12 7 12-7v14H0z"/></svg></span>
    <span class="s-red"><svg width="12" height="12" viewBox="0 0 12 12"><path d="M6 0v12M0 6h12" stroke="#fff" stroke-width="2"/></svg></span>
  </div>
</div>

<header class="abs header">
  <div class="abs brand">
    <div class="brand-name">Meridian Crest Legal Group</div>
    <div class="brand-tag">Divorce and Personal Injury Lawyers</div>
  </div>
  <nav class="abs nav"><a>Home</a><a>Practice Areas</a><a>Attorneys</a><a>Blog</a><a>Contact Us</a></nav>
</header>

<section class="abs hero" role="img" aria-label="Photo of classical courthouse stone columns against a blue sky">
  <svg class="abs" style="left:0;top:352px" width="300" height="159" viewBox="0 0 300 159"><path d="M0 0L300 159H0z" fill="#fff"/></svg>
  <svg class="abs" style="left:0;top:0" width="700" height="352" viewBox="0 0 700 352"><path d="M0 0H620L700 352H0z" fill="#fff" opacity=".45"/></svg>
  <div class="abs kicker">Kona Lawyers of MCLG -Legal kōkua with aloha.</div>
  <div class="abs sub">Over 70 years of combined practice</div>
  <h1 class="abs">Dedicated to making sure you receive the care and attention you need.</h1>
  <a class="abs btn">Get Started <svg width="16" height="16" viewBox="0 0 16 16"><circle cx="8" cy="8" r="8" fill="#7a2a10"/><path d="M5 8h6M8.5 5l3 3-3 3" stroke="#fff" stroke-width="1.8" fill="none"/></svg></a>
</section>

<div class="abs box b1">
  <h3>OUR CORE VALUES</h3>
  <ul>
    <li>Kōkua and aloha to our clients</li>
    <li>Commitment and dedication</li>
    <li>Licensed and experienced attorneys</li>
    <li>Flexibility to work around your needs</li>
    <li>Open communication</li>
    <li>Accurate assessment of your claim</li>
  </ul>
</div>
<div class="abs box b2">
  <h3>WE CARE</h3>
  <p>Our firm is designed to take care of our clients as ohana during traumatic times. That includes offering free consultations and discounted rates for our services.</p>
</div>
<div class="abs box b3">
  <h3>OUR LAWYERS</h3>
  <p>Our lawyers are board-certified specialists in all fields of our practice. With over 70 combined years experience, you're in good hands with us.</p>
</div>

<section class="about">
  <div class="abs label about-label">About Us</div>
  <h2 class="abs">Welcome to Kona Lawyers of MCLG</h2>
  <p class="abs lead">Lawyers Serving the Big Island and Neighboring Islands</p>
  <div class="abs copy">
    <p>The experienced attorneys in the Meridian Crest Legal Group's Kailua Kona, Hawaii office provide clients with a wide range of litigation expertise, including legal claims involving divorce &amp; family, personal injury, toxic exposures, intellectual property, and real estate.</p>
    <p>Our Kona office also offers commercial and hospitality litigation expertise on behalf of a wide variety of clients, including restaurants, hotels, property owners, and many others. We never wish to see our clients go to court, though if there is no other option, you're in safe hands with our seasoned trial lawyers and the many years of courtroom experience behind them.</p>
  </div>
  <a class="abs learn"><u>LEARN MORE</u> ABOUT THE KONA LAWYERS OF MCLG &nbsp;<span style="color:#a84f14">»</span></a>
  <div class="abs dots"><i></i><i></i></div>
</section>

<section>
  <div class="abs label prac-label">Expertise</div>
  <h2 class="abs prac-title">Areas of Practice</h2>
  <div class="abs tile t1" role="img" aria-label="Photo of a parent and child at home">
    <h3 style="top:36px">Family &amp; Divorce</h3>
    <p style="top:76px">MCLG's Kona-based lawyers are committed to providing quality and aggressive legal services that minimize the emotional and financial burdens...</p>
    <a class="more" style="top:164px">Read More »</a>
  </div>
  <div class="abs tile t2" role="img" aria-label="Photo of a damaged blue car after a collision">
    <h3 style="top:62px">Personal Injury</h3>
    <p style="top:102px">MCLG's Kona Lawyers are well versed in torts law and have expertise in all aspects of personal injury including medical malpractice,</p>
    <a class="more" style="top:190px">Read More »</a>
  </div>
  <div class="abs tile t3" role="img" aria-label="Photo of a restaurant kitchen pass under warm lamps">
    <h3 style="top:146px">Corporate &amp; Intellectual Property</h3>
    <p style="top:186px">MCLG's Hawaii corporate clients include restaurants, hotels, property owners, and many other types of organizations...</p>
    <a class="more" style="top:274px">Read More »</a>
  </div>
  <div class="abs tile t4" role="img" aria-label="Photo of timber house framing under construction">
    <h3 style="top:146px">Real Estate</h3>
    <p style="top:186px;width:440px">Meridian Crest Legal Group has its roots firmly planted in real estate. We are, at our core, a real estate law firm. Dale Kaneshiro is also a licensed...</p>
    <a class="more" style="top:274px">Read More »</a>
  </div>
</section>

<section>
  <div class="abs label team-label">Members</div>
  <h2 class="abs team-title">Our Team</h2>
  <div class="abs card c1">
    <h3>DALE KANESHIRO, ESQ.</h3>
    <p>Dale Kaneshiro graduated from the Pacific Coast University, Harbor College of Law, in 1972.</p>
    <a class="more">Read More »</a>
  </div>
  <div class="abs card c2">
    <h3>OWEN HALVORSEN, ESQ.</h3>
    <p>Owen Halvorsen graduated from the Pacific Coast University, Harbor College of Law, in 1971.</p>
    <a class="more">Read More »</a>
  </div>
  <div class="abs avatar a1" role="img" aria-label="Portrait photo of attorney Dale Kaneshiro"></div>
  <div class="abs avatar a2" role="img" aria-label="Portrait photo of attorney Owen Halvorsen"></div>
</section>

<section>
  <div class="abs blog" role="img" aria-label="Background photo of a sunlit interior in warm orange tones"></div>
  <div class="abs label blog-label">Updates</div>
  <h2 class="abs blog-title">Our Latest Blog</h2>
  <article class="abs post p1">
    <div class="img" role="img" aria-label="Photo of paper family cut-out figures"></div>
    <div class="date">FEB<br>15</div>
    <h3>TOP 10 THINGS TO DO BEFORE FILING FOR DIVORCE</h3>
    <p>Lorem ipsum dolor sit amet, consectetur adipiscing elit, sed do eiusmod tempor incididunt ut labore et dolore</p>
    <a class="more">Read More »</a>
  </article>
  <article class="abs post p2">
    <div class="img" role="img" aria-label="Photo of a gavel and stethoscope on papers"></div>
    <div class="date">FEB<br>15</div>
    <h3>TOP 15 THINGS TO DO DURING CUSTODY BATTLE</h3>
    <p>Lorem ipsum dolor sit amet, consectetur adipiscing elit, sed do eiusmod tempor incididunt ut labore et dolore</p>
    <a class="more">Read More »</a>
  </article>
  <article class="abs post p3">
    <div class="img" role="img" aria-label="Photo of a hand placing a small model house on documents"></div>
    <div class="date">FEB<br>15</div>
    <h3>TOP 10 THINGS TO DO BEFORE FILING FOR DIVORCE</h3>
    <p>Lorem ipsum dolor sit amet, consectetur adipiscing elit, sed do eiusmod tempor incididunt ut labore et dolore</p>
    <a class="more">Read More »</a>
  </article>
</section>

<section class="abs strip">
  <div class="abs social">
    <span class="s-blue1"></span><span class="s-blue2"></span>
    <span class="s-gray"><svg width="15" height="15" viewBox="0 0 24 24" fill="#fff"><path d="M6 2h12v6H6zM3 9h18v8h-3v5H6v-5H3zm5 7v4h8v-4z"/></svg></span>
    <span class="s-gray2"><svg width="15" height="12" viewBox="0 0 24 20" fill="#fff"><path d="M0 0h24v3L12 10 0 3zm0 6l12 7 12-7v14H0z"/></svg></span>
    <span class="s-red"><svg width="12" height="12" viewBox="0 0 12 12"><path d="M6 0v12M0 6h12" stroke="#fff" stroke-width="2"/></svg></span>
  </div>
  <div class="abs item i1"><span class="ico"><svg width="16" height="16" viewBox="0 0 24 24" fill="#7a2a10"><path d="M6.6 10.8a15 15 0 006.6 6.6l2.2-2.2c.3-.3.7-.4 1-.2 1.1.4 2.3.6 3.6.6.6 0 1 .4 1 1V20c0 .6-.4 1-1 1A17 17 0 013 4c0-.6.4-1 1-1h3.5c.6 0 1 .4 1 1 0 1.3.2 2.5.6 3.6.1.3 0 .7-.2 1z"/></svg></span>+1.808.555.0142</div>
  <div class="abs item i2"><span class="ico"><svg width="18" height="18" viewBox="0 0 24 24" fill="#7a2a10"><path d="M22 2L2 10l7 3 2 8 3-6 6 4z"/></svg></span>clients@tarnadvocate.example</div>
</section>

<footer>
  <div class="abs brand f-brand">
    <div class="brand-name">Meridian Crest Legal Group</div>
    <div class="brand-tag">Divorce and Personal Injury Lawyers</div>
  </div>
  <p class="abs f-text">Lorem ipsum dolor sit amet, consectetur adipiscing elit. Curabitur sed varius diam, et varius nisi. Nam lobortis, est a elementum molestie, sapien nunc malesuada lacus, viverra finibus diam ex rhoncus magna.</p>
  <div class="abs f-col fc1"><h4>Quick Links</h4><a>Home</a><a>Practice Areas</a><a>Attorneys</a><a>Blog</a><a>Contact Us</a></div>
  <div class="abs f-col fc2"><h4>Practice Areas</h4><a>Family &amp; Divorce</a><a>Personal Injury</a><a>Corporate &amp; Intellectual Property</a><a>Real Estate</a></div>
  <div class="abs f-col fc3"><h4>Newsletter</h4><div class="f-input">Enter Your Email Address</div><div class="f-btn">Subscribe</div></div>
  <div class="abs copy-line">Copyright © 2019 The Company Name, All Rights Reserved</div>
</footer>

</body>
</html>
```